veLuna - nutrition bars - logo and packaging*

veLuna develops stress-relief nutrition bars powered by deep profiling machine learning technology, offering personalized stress management routine.
We produce 3 flavors of nutrition bars. in each flavor, we produce 6 stress relief formulations (3 for day, 3 for night) in 2 strengths.

We need a rebranding of our logo and packaging.

Target Market(s)

Full description of the target audience and their needs and lifestyle is explained in the attached presentation

Logo Text

veLuna

Font styles to use
Script

Colors

Designer to choose colors to be used in the design.

Requirements
Must have
• logo
• Packaging
• Full description of the deliveries is explained in the attached presentation
Nice to have
• concept for boxes, website

```html
<!DOCTYPE html>
<html lang="en">
<head>
<meta charset="utf-8">
<title>veLuna – packaging layout options</title>
<link rel="stylesheet" href="https://fonts.googleapis.com/css2?family=Montserrat:wght@800&family=Nunito:wght@400;600;700&display=swap">
<style>
  :root{
    --bg-top:#e8e8e8;
    --bg-bottom:#a3a3a3;
    --wrapper:#f7f7f7;
    --ink:#111111;
    --logo:#8a949c;
    --muted:#7d7d7d;
    --green:#2e8a36;
    --pink:#c63a78;
    --yellow:#e2b714;
    --purple:#8a6aa8;
    --gray:#7f8e99;
    --blue:#3a55a6;
  }
  *{box-sizing:border-box;margin:0;padding:0}
  html,body{width:670px;height:1200px;overflow:hidden}
  body{
    position:relative;
    background:linear-gradient(180deg,var(--bg-top) 0%,#cfcfcf 50%,var(--bg-bottom) 100%);
    font-family:"Nunito",sans-serif;
  }
  .option-title{
    position:absolute;left:0;width:670px;text-align:center;
    font-family:"Montserrat",sans-serif;font-weight:800;font-size:22px;
    letter-spacing:2.4px;color:var(--ink);z-index:2;
  }
  .option-title--one{top:72px}
  .option-title--two{top:647px}
  .pointer{position:absolute;left:0;width:52px;height:14px;z-index:2}
  .pointer--one{top:366px}
  .pointer--two{top:878px}

  .pack{
    position:absolute;width:193px;height:525px;
    background:linear-gradient(90deg,#e6e6e6 0%,var(--wrapper) 12%,#ffffff 50%,var(--wrapper) 88%,#e2e2e2 100%);
    border-radius:4px;
    display:flex;flex-direction:column;align-items:center;
    padding-top:82px;
    box-shadow:0 4px 10px rgba(0,0,0,.12);
  }
  .pack::before,.pack::after{
    content:"";position:absolute;left:0;right:0;height:48px;
    background:repeating-linear-gradient(180deg,#eeeeee 0 3px,#f9f9f9 3px 6px);
  }
  .pack::before{top:0;border-radius:4px 4px 0 0}
  .pack::after{bottom:0;border-radius:0 0 4px 4px}
  .col-1{left:29px}.col-2{left:238px}.col-3{left:447px}
  .row-1{top:51px}.row-2{top:633px}

  .brand{
    width:150px;height:48px;text-align:center;
    font-weight:600;font-size:42px;line-height:48px;
    color:var(--logo);letter-spacing:-1px;
  }

  .pattern{width:140px;height:146px;margin-top:52px}
  .routine-icon{width:30px;height:24px;margin-top:10px;color:var(--muted)}
  .variant{
    width:151px;height:24px;margin-top:2px;
    color:#fff;font-weight:600;font-size:14px;
    display:flex;align-items:center;justify-content:center;
    border-radius:1px;
  }
  .formula{font-size:10.5px;color:var(--muted);margin-top:6px;white-space:nowrap}
  .ingredients-icon{width:44px;height:20px;margin-top:4px;border-radius:9px;
    background:linear-gradient(90deg,#d4d4d4,#bdbdbd)}
  .flavour{font-size:10.5px;letter-spacing:1.2px;color:var(--muted);margin-top:6px;white-space:nowrap}
  .weight{align-self:flex-start;margin-left:31px;font-size:11px;color:var(--muted)}
</style>
</head>
<body>

<h1 class="option-title option-title--one">arange middle design option 1 : bottom</h1>
<h1 class="option-title option-title--two">arange middle design option 2 : middle</h1>

<svg class="pointer pointer--one" viewBox="0 0 52 14"><line x1="0" y1="7" x2="48" y2="7" stroke="#111" stroke-width="2"/><path d="M40 1 L51 7 L40 13" fill="none" stroke="#111" stroke-width="2"/></svg>
<svg class="pointer pointer--two" viewBox="0 0 52 14"><line x1="0" y1="7" x2="48" y2="7" stroke="#111" stroke-width="2"/><path d="M40 1 L51 7 L40 13" fill="none" stroke="#111" stroke-width="2"/></svg>

<!-- Row 1 -->
<section class="pack col-1 row-1">
  <div class="brand">veLuna</div>
  <div class="pattern" role="img" aria-label="Green woven line pattern" style="background:linear-gradient(180deg,#d9ecd9,#b8dbba)"></div>
  <svg class="routine-icon" viewBox="0 0 30 24" aria-label="Day"><path d="M6 20 A9 9 0 0 1 24 20" fill="none" stroke="currentColor" stroke-width="2"/><line x1="2" y1="20" x2="28" y2="20" stroke="currentColor" stroke-width="2"/><line x1="15" y1="2" x2="15" y2="7" stroke="currentColor" stroke-width="2"/><line x1="5" y1="8" x2="8" y2="11" stroke="currentColor" stroke-width="2"/><line x1="25" y1="8" x2="22" y2="11" stroke="currentColor" stroke-width="2"/></svg>
  <div class="variant" style="background:var(--green)">Calm Green</div>
  <div class="formula">Plant Based Molecules</div>
  <div class="ingredients-icon" role="img" aria-label="Dates, apples and nuts"></div>
  <div class="flavour">Dates, Apples &amp; Nuts</div>
  <div class="weight">30 gr</div>
</section>

<section class="pack col-2 row-1">
  <div class="brand">veLuna</div>
  <div class="pattern" role="img" aria-label="Pink dotted wave pattern with plus sign" style="background:linear-gradient(180deg,#f6dbe7,#eec3d6)"></div>
  <svg class="routine-icon" viewBox="0 0 30 24" aria-label="Day"><path d="M6 20 A9 9 0 0 1 24 20" fill="none" stroke="currentColor" stroke-width="2"/><line x1="2" y1="20" x2="28" y2="20" stroke="currentColor" stroke-width="2"/><line x1="15" y1="2" x2="15" y2="7" stroke="currentColor" stroke-width="2"/><line x1="5" y1="8" x2="8" y2="11" stroke="currentColor" stroke-width="2"/><line x1="25" y1="8" x2="22" y2="11" stroke="currentColor" stroke-width="2"/></svg>
  <div class="variant" style="background:var(--pink)">Energetic Pink+</div>
  <div class="formula">Extra Plant Based Molecules</div>
  <div class="ingredients-icon" role="img" aria-label="Dates, apples and nuts"></div>
  <div class="flavour">Dates, Apples &amp; Nuts</div>
  <div class="weight">30 gr</div>
</section>

<section class="pack col-3 row-1">
  <div class="brand">veLuna</div>
  <div class="pattern" role="img" aria-label="Yellow flowing lines with dots" style="background:linear-gradient(180deg,#fbf0c8,#f5e19c)"></div>
  <svg class="routine-icon" viewBox="0 0 30 24" aria-label="Night"><path d="M14 3 A10 10 0 1 0 25 17 A8 8 0 0 1 14 3 Z" fill="none" stroke="currentColor" stroke-width="2"/><circle cx="23" cy="6" r="1.5" fill="currentColor"/></svg>
  <div class="variant" style="background:var(--yellow)">Focused Yellow</div>
  <div class="formula">Plant Based Molecules</div>
  <div class="ingredients-icon" role="img" aria-label="Oats, banana and pecan"></div>
  <div class="flavour">Oats, banana &amp; pecan</div>
  <div class="weight">30 gr</div>
</section>

<!-- Row 2 -->
<section class="pack col-1 row-2">
  <div class="brand">veLuna</div>
  <div class="pattern" role="img" aria-label="Purple wood-grain line pattern with plus sign" style="background:linear-gradient(180deg,#e8def1,#d6c7e6)"></div>
  <svg class="routine-icon" viewBox="0 0 30 24" aria-label="Night"><path d="M14 3 A10 10 0 1 0 25 17 A8 8 0 0 1 14 3 Z" fill="none" stroke="currentColor" stroke-width="2"/><circle cx="23" cy="6" r="1.5" fill="currentColor"/></svg>
  <div class="variant" style="background:var(--purple)">Relaxed Purple+</div>
  <div class="formula">Extra Plant Based Molecules</div>
  <div class="ingredients-icon" role="img" aria-label="Oats, banana and pecan"></div>
  <div class="flavour">Oats, banana &amp; pecan</div>
  <div class="weight">30 gr</div>
</section>

<section class="pack col-2 row-2">
  <div class="brand">veLuna</div>
  <div class="pattern" role="img" aria-label="Gray hexagon mesh pattern" style="background:linear-gradient(180deg,#ebeced,#d9dbdd)"></div>
  <svg class="routine-icon" viewBox="0 0 30 24" aria-label="Night"><path d="M14 3 A10 10 0 1 0 25 17 A8 8 0 0 1 14 3 Z" fill="none" stroke="currentColor" stroke-width="2"/><circle cx="23" cy="6" r="1.5" fill="currentColor"/></svg>
  <div class="variant" style="background:var(--gray)">Sleepy Gray</div>
  <div class="formula">Plant Based Molecules</div>
  <div class="ingredients-icon" role="img" aria-label="Dates, apples and nuts"></div>
  <div class="flavour">Dates, Apples &amp; Nuts</div>
  <div class="weight">30 gr</div>
</section>

<section class="pack col-3 row-2">
  <div class="brand">veLuna</div>
  <div class="pattern" role="img" aria-label="Blue connected-node network pattern with plus sign" style="background:linear-gradient(180deg,#dde3f3,#c4cfeb)"></div>
  <svg class="routine-icon" viewBox="0 0 30 24" aria-label="Night"><path d="M14 3 A10 10 0 1 0 25 17 A8 8 0 0 1 14 3 Z" fill="none" stroke="currentColor" stroke-width="2"/><circle cx="23" cy="6" r="1.5" fill="currentColor"/></svg>
  <div class="variant" style="background:var(--blue)">Comfortable Blue+</div>
  <div class="formula">Extra Plant Based Molecules</div>
  <div class="ingredients-icon" role="img" aria-label="Dates, apples and nuts"></div>
  <div class="flavour">Dates, Apples &amp; Nuts</div>
  <div class="weight">30 gr</div>
</section>

</body>
</html>
```